Letterhead Design for Law Firm

**Edit: I have added the photo of a bottom that I like.

------
We are looking for a re-design of our new letterhead. The letterhead is for a law firm and will be used for digital and traditionally printed correspondence.

Here are some suggestions:

- Please use colours are #8ec900 and simple black.
- Please do not use any type of "waves" at the bottom of the page. This is not in style at all.
- Please stay modern yet conservative.
- Please use font Segoe UI Light or similar if you can
- Avoid clipart or illustrations.
- Utilize ample white space in the layout so the design looks clean and information is easy to read at a glance. Don't overcrowd the letterhead.
- Make sure the letterhead design is consistent with our brand identity (see corvelith.ca)
-Please, no black headers or footers.

I am attaching my current letterhead and signature for your convenience.

Remember, the letterhead is an extension of our professional identity. We are a successful firm and trial lawyers who correspond with insurers, judges, lawyers, courts, clients, etc. Make it new, modern, attractive, yet powerful and conservative.

It needs to be easily printable. I would like the bleed removed in print so the black bar the bottom crosses the page (but the text is not near the edges)
Updates

Low design quality

Target Market(s)

Clients, Government Offices, Judiciary, Lawyers, Insurance Companies, Colleagues.

Industry/Entity Type

Law

Other font styles liked:
• Segoe UI LIght, Calibri Light,

Colors
00AB8E
00BBA5
67D7C9
C6EFE9
E9F9F6

Requirements
Must have
• Everything that is on the letterhead now.
Nice to have
• Cutting Edge design, yet conservative.
Should not have
• law firm cliche design, images,

```html
<!DOCTYPE html>
<html lang="en">
<head>
<meta charset="utf-8">
<title>Varnell Letterhead</title>
<link href="https://fonts.googleapis.com/css2?family=Open+Sans:wght@300;400;600;700&display=swap" rel="stylesheet">
<style>
  :root {
    --green: #8ec900;
    --ink: #1a1a1a;
    --muted: #333333;
    --paper: #ffffff;
    --backdrop: #d6d6d6;
  }
  * { box-sizing: border-box; margin: 0; padding: 0; }
  html, body { width: 1200px; height: 1155px; overflow: hidden; }
  body {
    background: var(--backdrop);
    font-family: "Open Sans", "Segoe UI", sans-serif;
    color: var(--ink);
    position: relative;
  }
  .letterhead {
    position: absolute;
    left: 165px; top: 14px;
    width: 870px; height: 1126px;
    background: var(--paper);
    overflow: hidden;
  }
  .firm-name {
    position: absolute; left: 88px; top: 150px;
    font-weight: 400; color: var(--ink); line-height: 1;
  }
  .firm-name .primary { display: block; font-size: 62px; letter-spacing: 1px; }
  .firm-name .secondary { display: block; font-size: 15px; letter-spacing: 3.5px; margin-top: 8px; }

  .contact {
    position: absolute; left: 560px; top: 58px;
    border-left: 2px solid var(--green);
    padding: 4px 0 6px 12px;
    font-size: 12px; line-height: 1.4; font-weight: 400; color: var(--muted);
  }
  .contact b { font-weight: 700; color: var(--ink); }
  .contact .web-accent { color: var(--green); font-weight: 600; }
  .contact .practice-title { margin-top: 12px; font-weight: 700; color: var(--ink); }

  .letter { position: absolute; left: 95px; top: 0; width: 690px; font-size: 14px; }
  .letter p { position: absolute; left: 0; white-space: nowrap; }
  .marking { font-weight: 600; }
  .date { top: 290px; left: 12px !important; font-weight: 300; }
  .recipient { font-weight: 300; line-height: 1.45; }

  .re-rule { position: absolute; left: 120px; width: 560px; height: 1px; background: var(--ink); }
  .subject { position: absolute; left: 290px; font-weight: 600; font-size: 14px; line-height: 1.5; }
  .subject sup { font-size: 9px; }

  .closing { position: absolute; left: 300px; top: 760px; font-size: 14px; }
  .closing .valediction { font-weight: 300; }
  .closing .firm-caps { font-weight: 400; }
  .signature-mark { display: block; width: 200px; height: 56px; margin: 8px 0 6px 20px;
    background: linear-gradient(90deg, #e9e9e9, #f6f6f6); border-radius: 3px; }
  .closing .signer { font-weight: 300; font-size: 15px; }
  .closing .corp { font-weight: 600; font-size: 13px; }
  .closing .meta { font-weight: 300; font-size: 13px; margin-left: 12px; line-height: 1.5; }

  .footer-rule { position: absolute; left: 0; width: 870px; }
  .footer-rule.ink { bottom: 30px; height: 4px; background: var(--ink); }
  .footer-rule.accent { bottom: 0; height: 24px; background: var(--green); }
</style>
</head>
<body>
  <div class="letterhead">
    <div class="firm-name">
      <span class="primary">VARNELL</span>
      <span class="secondary">PERSONAL INJURY LAWYERS</span>
    </div>

    <div class="contact">
      <div>www.<span class="web-accent">CORVELITH</span>.ca</div>
      <div>48 Harbour Street E., Suite 902</div>
      <div>Kingsford, ON&nbsp; K7P 3R2</div>
      <div><b>T:</b> 613-555-0142</div>
      <div><b>F:</b> 613-555-0187</div>
      <div><b>File Clerk:</b> Clara Whitfield</div>
      <div><b>Email:</b> clara@corvelith.ca</div>
      <div class="practice-title">Practice Restricted</div>
      <div>Serious Personal Injury</div>
      <div>Wrongful Death Litigation</div>
      <div>Long-Term Disability Litigation</div>
      <div>Wrongful Dismissal Litigation</div>
      <div>Employee Terminations</div>
    </div>

    <div class="letter">
      <p class="marking" style="top:255px;">Without Prejudice</p>
      <p class="date">March 13, 2024</p>
      <p class="marking" style="top:325px;left:20px;">By Email</p>
      <p class="recipient" style="top:360px;left:30px;">
        Northvale Insurance Company<br>
        Claims Litigation Department<br>
        27 Birchmount Avenue North<br>
        P.O. Box 4100<br>
        Guelton, ON&nbsp;&nbsp; N5K 2T8
      </p>
      <p class="recipient" style="top:478px;left:30px;">Attention:&nbsp; Mr. Dorian Pell</p>
      <p class="recipient" style="top:518px;left:30px;">Mr. Pell:</p>

      <div class="re-rule" style="top:552px;"></div>
      <p class="marking" style="top:566px;left:30px;">Re:</p>
      <div class="subject" style="top:562px;">
        Marsh v. Delacorte et al.<br>
        DOL:&nbsp; September 12, 2019<br>
        Pre-Mediation Settlement Proposal – March 13<sup>th</sup>, 2024
      </div>
      <div class="re-rule" style="top:636px;"></div>
    </div>

    <div class="closing">
      <div class="valediction">Yours very truly,</div>
      <div class="firm-caps">VARNELL PERSONAL INJURY LAWYERS</div>
      <span class="signature-mark" role="img" aria-label="Handwritten signature of Owen T. Varnell"></span>
      <div class="signer">Owen T. Varnell</div>
      <div class="corp">Varnell Law Professional Corporation</div>
      <div class="meta">/cw<br>Encl.</div>
    </div>

    <div class="footer-rule ink" aria-hidden="true"></div>
    <div class="footer-rule accent" aria-hidden="true"></div>
  </div>
</body>
</html>
```